Willow Cradle Pregnancy and Baby Massage

I need a web design for a new business, WILLOW CRADLE PREGNANCY AND BABY MASSAGE that I am in the process of setting up in the suburbs of Perth, Western Australia. The business is owned and operated by myself and my intention is to service Pregnant Mothers and Parents of Young Babies that would benefit from massage. I would like to have a "Home Page" and pages for "About Me", "Pregnancy Massage", "Baby Massage", a Pricing Page for Pregnancy Massage Sessions, a Pricing Page for Baby Massage Sessions, and a "Contact Me" page to allow clients to either contact me with queries or book available pregnancy massage sessions on a particular day of the week. I would also like a "News" page that would include articles I have written, news about new courses and a link to my Facebook page (yet to be set up). I would like to keep the colour schemes similar to my logo design colours. I need the design to be easy to follow and to appeal to a younger audience (20's to mid 30's).
The target audience is pregnant mothers-to-be wishing to receive massage treatments, and new parents and grandparents of small babies that would like to learn how to massage their babies.
The look and feel should be modern, professional, elegant and feminine.
I need the design to be in a standard format such that I can update the content by myself ( and does not need specialised software) as the company and business progresses.

Target Market(s)

Contact Information for Business Card

Card should have rounded edges. Design should have the same "feel" as the website. Contact Details of my business address, mobile phone, email and website should be included.

Font styles to use
Script

Requirements
Must have
• Same colours as logo design. In cmyk system, the colours are: 20,60,0,0 which best result is pantone 681 and 40,40,0,0 which best result is pantone 2645. Card should include the logo design.

```html
<!DOCTYPE html>
<html lang="en">
<head>
<meta charset="utf-8">
<title>Willow Cradle Pregnancy and Baby Massage</title>
<link href="https://fonts.googleapis.com/css2?family=Great+Vibes&family=Open+Sans:wght@400;600;700&display=swap" rel="stylesheet">
<style>
:root{
  --plum:#b0609f;
  --plum-dark:#94478a;
  --lilac:#a48fc4;
  --lilac-soft:#e9def0;
  --ink:#4a4a4a;
  --muted:#7a7a7a;
  --dark:#2f2d30;
  --light:#f3f1f3;
  --white:#fff;
}
*{box-sizing:border-box;margin:0;padding:0}
html,body{width:1200px;height:4232px;overflow:hidden}
body{font-family:"Open Sans",Arial,sans-serif;color:var(--ink);background:var(--white);position:relative}
.abs{position:absolute}
.script{font-family:"Great Vibes",cursive;font-weight:400}
.photo{position:absolute}
.btn{position:absolute;background:var(--plum);color:#fff;font-size:17px;font-weight:600;letter-spacing:1px;text-transform:uppercase;display:flex;align-items:center;justify-content:center}
.body-text{font-size:15px;line-height:1.55;color:var(--ink)}

/* header */
.brand{left:120px;top:10px;display:flex;align-items:center;gap:12px}
.brand-dot{width:46px;height:46px;border-radius:50%;background:var(--plum)}
.brand-name{font-size:22px;font-weight:600;color:var(--plum);line-height:1.1;width:200px}
.call{right:80px;top:42px;display:flex;align-items:center;gap:14px;color:var(--plum);font-size:17px;letter-spacing:1px}
.call-num{border:2px solid var(--plum);border-radius:22px;padding:6px 16px;font-weight:600}

.nav{left:0;top:124px;width:1200px;height:50px;background:var(--plum);display:flex;align-items:center;padding-left:70px}
.nav a{color:#fff;text-decoration:none;font-size:16px;padding:0 15px;height:50px;display:flex;align-items:center}
.nav a.active{background:var(--lilac)}

/* hero */
.hero{left:0;top:174px;width:1200px;height:590px;background:linear-gradient(100deg,#efe9ec 0%,#d9cdd3 40%,#c8b8bf 70%,#e6dde2 100%)}
.hero-title{left:120px;top:385px;width:660px;text-align:center;color:var(--plum);font-size:96px;line-height:1}
.hero-sub{left:120px;top:485px;width:660px;text-align:center;color:var(--plum);font-size:40px}
.booking{left:790px;top:188px;width:330px;height:272px;background:rgba(176,96,159,.88);padding:12px 18px}
.booking h3{color:#fff;font-size:20px;font-weight:600;text-align:center;letter-spacing:1px;margin-bottom:8px}
.field{height:32px;background:#fff;margin-bottom:8px;font-size:13px;color:var(--muted);padding:7px 10px}
.booking .submit{margin:6px auto 0;width:130px;height:34px;background:var(--lilac);color:#fff;font-weight:600;display:flex;align-items:center;justify-content:center;letter-spacing:1px}
.hero-rule{left:0;top:760px;width:1200px;height:6px;background:var(--plum)}
.hero-circle{left:500px;top:660px;width:200px;height:200px;border-radius:50%;border:8px solid #fff;box-shadow:0 0 0 4px var(--plum);background:radial-gradient(circle,#e7c7b5,#b98f7e)}

/* about */
.section-title{color:var(--plum);font-size:70px;line-height:1;white-space:nowrap}
.about-title{left:70px;top:870px}
.about-title small{font-size:58px}
.about-rule{left:70px;top:950px;width:180px;height:3px;background:var(--plum)}
.about-text{left:70px;top:970px;width:580px}
.about-circle{left:850px;top:860px;width:260px;height:260px;border-radius:50%;border:6px solid var(--plum);background:radial-gradient(circle,#f3d9cc,#d5a896)}
.about-small{left:670px;top:1060px;width:150px;height:150px;border-radius:50%;border:6px solid var(--plum);background:radial-gradient(circle,#e9c4b2,#b88a77)}
.play{left:945px;top:955px;width:70px;height:70px;border-radius:50%;background:rgba(255,255,255,.9);border:3px solid var(--plum)}

/* services */
.services{left:0;top:1280px;width:1200px;height:690px;background:linear-gradient(180deg,#3b383c,#29272a)}
.svc-title{color:#fff;font-size:62px;text-align:center;width:460px}
.svc-photo{border:6px solid #fff;width:440px;height:280px}
.svc-badge{width:110px;height:110px;border-radius:50%;background:#fff;border:5px solid var(--plum)}
.svc-text{color:#e7e2e7;font-size:14px;line-height:1.5;width:420px;text-align:center}
.divider{left:598px;top:1320px;width:2px;height:610px;background:rgba(255,255,255,.35)}

/* baby sessions */
.foot-photo{left:0;top:1970px;width:520px;height:460px;background:linear-gradient(120deg,#f4e3dc,#e6c3b3 60%,#fbf3ef)}
.sessions-title{left:545px;top:2000px;font-size:64px}
.sessions-sub{left:545px;top:2090px;font-size:19px;color:var(--ink);font-weight:600}
.list{font-size:15px;color:var(--ink);line-height:1.9;list-style:none}
.list li{display:flex;align-items:center;gap:10px}
.tick{width:14px;height:14px;border:2px solid var(--plum);border-radius:3px;flex:none}
.sub-list{margin-left:24px;font-size:14px;color:var(--muted);line-height:1.8;list-style:none}

/* pregnancy session */
.preg-title{left:70px;top:2478px;font-size:54px}
.preg-rule{left:70px;top:2545px;width:180px;height:3px;background:var(--plum)}
.preg-text{left:70px;top:2560px;width:480px}
.preg-photo{left:640px;top:2440px;width:560px;height:340px;background:linear-gradient(90deg,#f1ddd2,#d9ae9a 60%,#c89986)}
.preg-circle{left:575px;top:2640px;width:140px;height:140px;border-radius:50%;background:#fff;border:5px solid var(--plum)}

/* blog */
.blog{left:0;top:2850px;width:1200px;height:540px;background:var(--light)}
.blog-title{left:0;top:2880px;width:1200px;text-align:center}
.card{top:2980px;width:320px}
.card-photo{height:210px;position:relative}
.date{position:absolute;left:0;top:0;width:70px;height:70px;background:var(--plum);color:#fff;text-align:center;font-size:30px;font-weight:600;line-height:1;padding-top:10px}
.date span{display:block;font-size:12px;font-weight:400;margin-top:4px}
.card h4{color:var(--plum);font-size:19px;font-weight:600;margin:14px 0 6px}
.card p{font-size:14px;line-height:1.5}
.read{color:var(--plum);font-size:14px;font-weight:600;margin-top:12px;letter-spacing:1px}

/* publication */
.pub-title{left:70px;top:3440px}
.pub-rule{left:70px;top:3512px;width:180px;height:3px;background:var(--plum)}
.pub-text{left:70px;top:3530px;width:640px}
.book{left:880px;top:3380px;width:270px;height:250px;background:linear-gradient(135deg,#c47ab3,#9a4f8c);transform:rotate(-14deg);border-radius:6px}
.badge{left:480px;top:3745px;width:240px;height:130px;background:#fff;border:3px solid var(--lilac)}

/* footer */
.footer{left:0;top:3920px;width:1200px;height:312px;background:var(--plum)}
.foot-nav{left:0;top:3946px;width:1200px;display:flex;justify-content:center;gap:4px;color:#fff;font-size:14px}
.foot-nav span::after{content:"|";margin-left:8px;opacity:.6}
.foot-nav span:last-child::after{content:""}
.foot-rule{left:80px;top:3980px;width:1040px;height:1px;background:rgba(255,255,255,.5)}
.fcol{top:4000px;width:300px;text-align:center;color:#fff;font-size:14px;line-height:1.5}
.ficon{width:62px;height:62px;border-radius:50%;background:#fff;margin:0 auto 12px;display:flex;align-items:center;justify-content:center}
.bottom{left:0;top:4180px;width:1200px;height:52px;background:var(--plum-dark)}
.bottom-name{left:80px;top:4193px;color:#fff;font-size:17px;font-weight:600}
.bottom-copy{left:260px;top:4197px;color:#f0dcea;font-size:12px}
.socials{right:80px;top:4190px;display:flex;gap:12px}
.socials i{width:32px;height:32px;border-radius:50%;background:#fff;display:block}
</style>
</head>
<body>

<header>
  <div class="abs brand"><div class="brand-dot"></div><div class="brand-name">Willow Cradle</div></div>
  <div class="abs call"><span>CALL US NOW</span><span class="call-num">041 555 0192</span></div>
</header>

<nav class="abs nav">
  <a class="active">Home</a><a>About Me</a><a>Pregnancy Massage</a><a>Baby Massage</a><a>Pregnancy Massage Sessions</a><a>Baby Massage Sessions</a><a>Contact us</a>
</nav>

<section>
  <div class="photo hero" role="img" aria-label="Pregnant woman relaxing during a massage"></div>
  <h1 class="abs hero-title script">Willow Cradle</h1>
  <p class="abs hero-sub script">Pregnancy and Baby Massage</p>
  <form class="abs booking">
    <h3>BOOK APPOINTMENT</h3>
    <div class="field">Name</div><div class="field">Email</div><div class="field">Phone</div><div class="field">Message</div>
    <div class="submit">SUBMIT</div>
  </form>
  <div class="abs hero-rule"></div>
  <div class="photo hero-circle" role="img" aria-label="Hands resting on a pregnant belly"></div>
</section>

<section>
  <h2 class="abs section-title script about-title"><small>about</small> Willow Cradle</h2>
  <div class="abs about-rule"></div>
  <p class="abs about-text body-text">Willow Cradle Pregnancy and Baby Massage was launched in 2017, offering massage for pregnant women, and instruction of baby massage to parents, grandparents and carers. My vision is to provide a professional massage service to pregnant mothers and babies that benefits from my skills and experience as a midwife. My appointment is one that offers each session my clients should leave feeling relaxed, calm, emotionally nurtured, soothed and supported. Best times, I will bear the utmost care of your privacy, safety and comfort to enter a very personal, intimate time in your life.</p>
  <div class="btn" style="left:70px;top:1185px;width:190px;height:52px">Learn More</div>
  <div class="photo about-circle" role="img" aria-label="Pregnant belly cradled by hands"></div>
  <div class="abs play"><svg width="64" height="64" viewBox="0 0 64 64"><path d="M26 20 L46 32 L26 44Z" fill="#b0609f"/></svg></div>
  <div class="photo about-small" role="img" aria-label="Mother holding her newborn"></div>
</section>

<section>
  <div class="abs services"></div>
  <h2 class="abs svc-title script" style="left:70px;top:1320px">Pregnancy Massage</h2>
  <h2 class="abs svc-title script" style="left:670px;top:1320px">Baby Massage</h2>
  <div class="photo svc-photo" style="left:80px;top:1410px;background:linear-gradient(120deg,#e9d7cf,#b88f84 60%,#6b4d4a)" role="img" aria-label="Therapist massaging a pregnant client"></div>
  <div class="photo svc-photo" style="left:680px;top:1410px;background:linear-gradient(120deg,#f6e8e0,#e2bfae 60%,#cfa08c)" role="img" aria-label="Baby receiving a gentle massage"></div>
  <div class="abs svc-badge" style="left:245px;top:1640px"></div>
  <div class="abs svc-badge" style="left:845px;top:1640px"></div>
  <p class="abs svc-text" style="left:90px;top:1760px">Lorem Ipsum is simply dummy text of the printing and typesetting industry. Lorem Ipsum has been the industry's standard dummy text ever since the 1500s.</p>
  <p class="abs svc-text" style="left:690px;top:1760px">Lorem Ipsum is simply dummy text of the printing and typesetting industry. Lorem Ipsum has been the industry's standard dummy text ever since the 1500s.</p>
  <div class="btn" style="left:225px;top:1860px;width:200px;height:52px">More Details</div>
  <div class="btn" style="left:760px;top:1860px;width:200px;height:52px">More Details</div>
  <div class="abs divider"></div>
</section>

<section>
  <div class="photo foot-photo" role="img" aria-label="Baby's foot held in an adult's hand"></div>
  <h2 class="abs section-title script sessions-title">Baby Massage Sessions</h2>
  <p class="abs sessions-sub">Baby Massage Course</p>
  <ul class="abs list" style="left:545px;top:2130px;width:260px">
    <li><i class="tick"></i>Permission sequence</li>
    <li><i class="tick"></i>Which Oils to Use</li>
    <li><i class="tick"></i>Basic massage techniques for:</li>
  </ul>
  <ul class="abs sub-list" style="left:545px;top:2232px">
    <li>o Legs</li><li>o Abdomen</li><li>o Chest</li><li>o Back</li>
  </ul>
  <ul class="abs list" style="left:830px;top:2130px;width:340px">
    <li><i class="tick"></i>When is the best time to massage your baby</li>
    <li><i class="tick"></i>Contraindications</li>
  </ul>
</section>

<section>
  <h2 class="abs section-title script preg-title">Pregnancy Massage Session</h2>
  <div class="abs preg-rule"></div>
  <p class="abs preg-text body-text">Each session begins with a consultation to assess any high risk factors, and to review any changes the body has undergone since the last session. This way the massage can be given in a safe manner. Each session begins with a consultation to assess any high risk factors, and to review any changes the body has undergone since the last session. This way the massage can be given in a safe manner.</p>
  <div class="btn" style="left:70px;top:2782px;width:200px;height:52px">More Details</div>
  <div class="photo preg-photo" role="img" aria-label="Hands forming a heart on a pregnant belly"></div>
  <div class="abs preg-circle"></div>
</section>

<section>
  <div class="abs blog"></div>
  <h2 class="abs section-title script blog-title">Latest Blog</h2>
  <article class="abs card" style="left:70px">
    <div class="card-photo" style="background:linear-gradient(120deg,#d9b59c,#8a6a55)" role="img" aria-label="Group of hands stacked together"><div class="date">14<span>MAR</span></div></div>
    <h4>Lorem Ipsum is simply text Dummy</h4>
    <p>Lorem Ipsum is simply dummy text of the printing and typesetting industry.</p>
    <p class="read">READ MORE &rsaquo;</p>
  </article>
  <article class="abs card" style="left:440px">
    <div class="card-photo" style="background:linear-gradient(180deg,#cfe0ee,#a6c48f)" role="img" aria-label="Pregnant woman doing yoga outdoors"><div class="date">26<span>JAN</span></div></div>
    <h4>Lorem Ipsum is simply text Dummy</h4>
    <p>Lorem Ipsum is simply dummy text of the printing and typesetting industry.</p>
    <p class="read">READ MORE &rsaquo;</p>
  </article>
  <article class="abs card" style="left:810px">
    <div class="card-photo" style="background:linear-gradient(180deg,#f5d48a,#d79a58 55%,#7e8f4e)" role="img" aria-label="Pregnant woman in a field at sunset"><div class="date">15<span>OCT</span></div></div>
    <h4>Lorem Ipsum is simply text Dummy</h4>
    <p>Lorem Ipsum is simply dummy text of the printing and typesetting industry.</p>
    <p class="read">READ MORE &rsaquo;</p>
  </article>
</section>

<section>
  <h2 class="abs section-title script pub-title">Our Publication</h2>
  <div class="abs pub-rule"></div>
  <p class="abs pub-text body-text">Lorem Ipsum is simply dummy text of the printing and typesetting industry. Lorem Ipsum has been the industry's standard dummy text ever since the 1500s, when an unknown printer took a galley of type and scrambled it to make a type specimen book.</p>
  <div class="btn" style="left:70px;top:3620px;width:170px;height:52px">Buy Now</div>
  <div class="photo book" role="img" aria-label="Cover of the published massage guide"></div>
  <div class="abs badge" role="img" aria-label="Certification badge"></div>
</section>

<footer>
  <div class="abs footer"></div>
  <div class="abs foot-nav"><span>Home</span><span>About Me</span><span>Pregnancy Massage</span><span>Baby Massage</span><span>Pregnancy Massage Sessions</span><span>Baby Massage Sessions</span><span>Contact us</span></div>
  <div class="abs foot-rule"></div>
  <div class="abs fcol" style="left:80px">
    <div class="ficon"><svg width="30" height="30" viewBox="0 0 24 24"><path d="M12 2a7 7 0 0 0-7 7c0 5 7 13 7 13s7-8 7-13a7 7 0 0 0-7-7zm0 9.5A2.5 2.5 0 1 1 12 6.5a2.5 2.5 0 0 1 0 5z" fill="#b0609f"/></svg></div>
    Maren Ellis<br>12 Example Lane, Perth, Australia
  </div>
  <div class="abs fcol" style="left:450px">
    <div class="ficon"><svg width="28" height="28" viewBox="0 0 24 24"><path d="M6.6 10.8a15 15 0 0 0 6.6 6.6l2.2-2.2c.3-.3.7-.4 1-.2 1.1.4 2.3.6 3.6.6.6 0 1 .4 1 1V20c0 .6-.4 1-1 1A17 17 0 0 1 3 4c0-.6.4-1 1-1h3.5c.6 0 1 .4 1 1 0 1.300.2 2.5.6 3.6.1.3 0 .7-.2 1z" fill="#b0609f"/></svg></div>
    041 555 0192
  </div>
  <div class="abs fcol" style="left:820px">
    <div class="ficon"><svg width="30" height="30" viewBox="0 0 24 24"><path d="M3 5h18v14H3z" fill="none" stroke="#b0609f" stroke-width="2"/><path d="M3 5l9 8 9-8" fill="none" stroke="#b0609f" stroke-width="2"/></svg></div>
    hello@willowcradle.example
  </div>
  <div class="abs bottom"></div>
  <div class="abs bottom-name">Willow Cradle</div>
  <div class="abs bottom-copy">| Copyright 2017. All Rights Reserved</div>
  <div class="abs socials"><i></i><i></i><i></i><i></i></div>
</footer>

</body>
</html>
```